Brightline Energy Product Distribution Brochure

We are looking to have our current brochure for our customers completely redesigned...the idea is to present the relevant information in an attractive way . Our website is brightlineenergyco.example where you can find more information about us. We have included a file with a rough idea of the page order and what each should include but feel free to adapt based on design. The example provided is only for context and doesnt have to be maintained. We will be using the brochure both digitally and in print form. As long as it reads easily and is eye catching, the design can be horizontal or vertical.Final deliverable should be indesign file.

"Our Brands" page: should be limited to one page (space being enough) where it has the header for each one (for example diesel generators) space for one or two lines of text and then the corresponding logos for each of the five categories
Updates

For those asking: the "our brands" page should be a single page layout where there is a header with the corresponding section and space for maybe one line of text followed by the two logos for that category. Each of the product pages should be similar in fashion to the one in the document attached: a photo of the product with some white space and space for the text to be included. We will be posting additional examples today

Target Market(s)

We want to present it to customers both digitally and in print so they can see our products

Industry/Entity Type

Power Generation

Font styles to use
Serif

Requirements
Must have
• Eye catching and able to present the information in a presentable fashion. Rest is up to you.
Nice to have
• Should incorporate the colors of our logo but can also add other depending on design

```html
<!DOCTYPE html>
<html lang="en">
<head>
<meta charset="utf-8">
<title>Brightline Energy – Distributor Program Guide</title>
<link href="https://fonts.googleapis.com/css2?family=Montserrat:wght@300;400;600;700&display=swap" rel="stylesheet">
<style>
  :root {
    --stage: #5e5e5e;
    --paper: #f4f4f4;
    --yellow: #efb71f;
    --yellow-pale: #f3dfa3;
    --yellow-soft: #f8ebc3;
    --charcoal: #3f3b3b;
    --ink: #3a3a3a;
    --grey-text: #555555;
  }
  * { margin: 0; padding: 0; box-sizing: border-box; }
  html, body { width: 1200px; height: 840px; overflow: hidden; }
  body { background: var(--stage); font-family: "Montserrat", sans-serif; }
  .cover {
    position: absolute; left: 320px; top: 24px;
    width: 560px; height: 792px;
    background: var(--paper);
    box-shadow: 0 10px 30px rgba(0,0,0,.35);
    overflow: hidden;
  }
  .cover-shapes { position: absolute; inset: 0; }
  .brand {
    position: absolute; left: 56px; top: 62px;
    display: flex; align-items: center; gap: 12px;
  }
  .brand-square { width: 26px; height: 26px; background: var(--yellow); }
  .brand-name {
    font-weight: 600; font-size: 22px; letter-spacing: 1px;
    color: var(--ink); text-transform: uppercase;
  }
  .title-block { position: absolute; left: 56px; top: 128px; }
  .title-main {
    font-weight: 700; font-size: 36px; letter-spacing: 1px;
    color: var(--yellow); line-height: 1.1;
  }
  .title-sub {
    font-weight: 300; font-size: 32px; letter-spacing: 1px;
    color: var(--grey-text); line-height: 1.15;
  }
  .title-rule { width: 170px; height: 2px; background: var(--grey-text); margin: 12px 0 12px; }
  .title-products {
    font-weight: 400; font-size: 17px; letter-spacing: 1px;
    color: var(--yellow); line-height: 1.35; text-transform: uppercase;
  }
</style>
</head>
<body>
  <main class="cover">
    <svg class="cover-shapes" viewBox="0 0 560 792" width="560" height="792" aria-hidden="false">
      <polygon class="accent-pale" points="560,190 360,372 560,372" fill="var(--yellow-pale)"/>
      <polygon class="accent-soft" points="560,280 460,372 560,372" fill="var(--yellow-soft)"/>
      <rect class="band-left-tint" x="0" y="356" width="60" height="16" fill="var(--yellow-soft)"/>
      <rect class="yellow-band" x="10" y="372" width="550" height="34" fill="var(--yellow)"/>
      <polygon class="charcoal-wedge" points="0,372 22,372 92,700 0,700" fill="var(--charcoal)"/>
      <defs>
        <linearGradient id="photoTone" x1="0" y1="0" x2="1" y2="1">
          <stop offset="0" stop-color="#c9b98a"/>
          <stop offset=".45" stop-color="#9aa58e"/>
          <stop offset=".7" stop-color="#8fb3c4"/>
          <stop offset="1" stop-color="#cfe1ec"/>
        </linearGradient>
      </defs>
      <polygon class="cover-photo" role="img" aria-label="Photo of a modern office tower with glass facade, trees and blue sky"
        points="34,420 560,420 560,672 90,672" fill="url(#photoTone)"/>
      <rect class="photo-foot-bar" x="92" y="676" width="58" height="8" fill="var(--yellow)"/>
    </svg>

    <div class="brand">
      <span class="brand-square"></span>
      <span class="brand-name">Brightline Energy</span>
    </div>

    <header class="title-block">
      <h1 class="title-main">DISTRIBUTOR</h1>
      <p class="title-sub">PROGRAM GUIDE</p>
      <div class="title-rule"></div>
      <p class="title-products">Diesel Generators,<br>Alternators &amp; Parts</p>
    </header>
  </main>
</body>
</html>
```